Business Cards for company that supports physicians that do medical research

Need to create a business card for Qorvel Studies (www.qorvelstudies.example), a company devoted to supporting physicians who conduct medical research. The form of the card should match the message of research and information quest. I have provided the logo of the company as an uploaded file. Designs should be simple and slick aimed at very high end clients.

Target Market(s)

Medical doctors that are also researchers

Industry/Entity Type

Medical

Contact Information for Business Card

Should feature logo and fields for personal info:
Name/title
Phone /email

Font styles to use
Serif
Sans Serif

Requirements
Must have
• Qorvel logo and fields for personal info:
• Name: Bertrand Okonfu
• Title: VP Research and Senior Analyst
• Phone: 555-203-4719
• email: info@qorvelstudies.example
Nice to have
• Interesting cards that I've seen:
• 1- all black/charcoal or very dark background
• 2- Plastic - semi-transparent
• 3- non-standard height-width ratios
• 4- Functional cards -- USB drive incorporated
Should not have
• Too busy; needs to stay very simple

```html
<!DOCTYPE html>
<html lang="en">
<head>
<meta charset="utf-8">
<title>Qorvel Studies — Business Card</title>
<link rel="stylesheet" href="https://fonts.googleapis.com/css2?family=Open+Sans:ital,wght@0,400;0,600;1,400&display=swap">
<style>
  :root {
    --backdrop: #3b3b3b;
    --card-white: #f7f7f7;
    --brand-blue: #1a7bbd;
    --brand-green: #3aae49;
    --ink: #4a4a4a;
    --white: #ffffff;
  }
  * { box-sizing: border-box; margin: 0; padding: 0; }
  html, body {
    width: 1200px;
    height: 750px;
    overflow: hidden;
    background: var(--backdrop);
    font-family: "Open Sans", sans-serif;
  }
  .canvas {
    position: relative;
    width: 1200px;
    height: 750px;
  }
  .card {
    position: absolute;
    top: 228px;
    width: 461px;
    height: 262px;
  }
  .card--front {
    left: 124px;
    background: var(--card-white);
  }
  .card--back {
    left: 618px;
    background: var(--brand-blue);
  }

  /* Front */
  .front-wordmark {
    position: absolute;
    right: 28px;
    top: 40px;
    display: flex;
    align-items: center;
    gap: 8px;
    font-size: 24px;
    font-weight: 600;
    color: var(--brand-blue);
    letter-spacing: 0.5px;
  }
  .wordmark-dot {
    width: 12px;
    height: 12px;
    border-radius: 50%;
    background: var(--brand-green);
  }
  .accent-bar {
    position: absolute;
    left: 0;
    top: 149px;
    width: 7px;
    height: 94px;
    background: var(--brand-blue);
  }
  .person {
    position: absolute;
    left: 25px;
    top: 145px;
  }
  .person-name {
    font-size: 16px;
    font-weight: 600;
    color: var(--brand-blue);
    line-height: 20px;
  }
  .person-title {
    font-size: 12px;
    color: var(--brand-green);
    line-height: 17px;
  }
  .contact-list {
    list-style: none;
    margin-top: 9px;
  }
  .contact-item {
    display: flex;
    align-items: center;
    gap: 6px;
    font-size: 11px;
    color: var(--ink);
    line-height: 17.5px;
  }
  .contact-icon {
    width: 11px;
    height: 11px;
    fill: var(--brand-blue);
    flex: none;
  }

  /* Back */
  .back-wordmark {
    position: absolute;
    right: 28px;
    top: 170px;
    font-size: 24px;
    font-weight: 600;
    color: var(--white);
    letter-spacing: 0.5px;
  }
  .back-url {
    position: absolute;
    right: 28px;
    top: 229px;
    font-size: 10.5px;
    font-style: italic;
    letter-spacing: 1.2px;
    color: var(--white);
  }
</style>
</head>
<body>
<main class="canvas">

  <section class="card card--front" aria-label="Business card front">
    <div class="front-wordmark">
      <span class="wordmark-dot"></span>
      <span>Qorvel Studies</span>
    </div>

    <div class="accent-bar"></div>

    <div class="person">
      <p class="person-name">Bertrand Okonfu</p>
      <p class="person-title">VP Research &amp; Senior Analyst</p>
      <ul class="contact-list">
        <li class="contact-item">
          <svg class="contact-icon" viewBox="0 0 24 24" aria-hidden="true">
            <path d="M6.6 10.8a15.1 15.1 0 0 0 6.6 6.6l2.2-2.2c.3-.3.7-.4 1-.2 1.1.4 2.3.6 3.6.6.6 0 1 .4 1 1V20c0 .6-.4 1-1 1C10.6 21 3 13.4 3 4c0-.6.4-1 1-1h3.5c.6 0 1 .4 1 1 0 1.3.2 2.5.6 3.6.1.3 0 .7-.2 1L6.6 10.8z"/>
          </svg>
          <span>555-203-4719</span>
        </li>
        <li class="contact-item">
          <svg class="contact-icon" viewBox="0 0 24 24" aria-hidden="true">
            <path d="M2 5h20v14H2z M4 7v.5l8 5 8-5V7l-8 5z" fill-rule="evenodd"/>
          </svg>
          <span>info@qorvelstudies.example</span>
        </li>
        <li class="contact-item">
          <svg class="contact-icon" viewBox="0 0 24 24" aria-hidden="true">
            <circle cx="12" cy="12" r="10"/>
            <path d="M2 12h20M12 2c3 3 3 17 0 20M12 2c-3 3-3 17 0 20" stroke="#ffffff" stroke-width="1.4" fill="none"/>
          </svg>
          <span>www.qorvelstudies.example</span>
        </li>
      </ul>
    </div>
  </section>

  <section class="card card--back" aria-label="Business card back">
    <div class="back-wordmark">Qorvel Studies</div>
    <p class="back-url">www.qorvelstudies.example</p>
  </section>

</main>
</body>
</html>
```